SkyvornQ Business Cards and Stationary Design

Need a design for our business cards and stationary. I want to carry on the theme of the logo. I want the business cards to have a design on the back. I would like the business cards and the stationary to carry the same theme, design scheme, and branding

Target Market(s)

Airlines and Maintenance Facilities

Industry/Entity Type

Aviation

Contact Information for Business Card

Name
Position Title
Address: 4827 Trellis Hollow Road, Brinmoor Bay, Calvera, 34951
Office Number
Mobile Number
Email
Website

Font styles to use
Serif
Sans Serif

Colors

Designer to choose colors to be used in the design.

```html
<!DOCTYPE html>
<html lang="en">
<head>
<meta charset="utf-8">
<title>SkyvornQ Business Card</title>
<link rel="stylesheet" href="https://fonts.googleapis.com/css2?family=Work+Sans:wght@300;400;700&display=swap">
<style>
  :root {
    --backdrop: #e9e7e4;
    --card: #ffffff;
    --navy: #17295a;
    --blue-light: #27a3df;
    --blue-mid: #1a70bb;
    --blue-deep: #1f3673;
    --text-grey: #555a66;
    --text-dark: #333844;
    --divider: #2a3559;
  }
  * { margin: 0; padding: 0; box-sizing: border-box; }
  html, body {
    width: 1200px; height: 960px; overflow: hidden;
    background: var(--backdrop);
    font-family: "Work Sans", Arial, sans-serif;
  }
  .canvas { position: relative; width: 1200px; height: 960px; }
  .card {
    position: absolute; left: 270px; width: 664px; height: 380px;
    background: var(--card); overflow: hidden;
    box-shadow: 0 6px 14px rgba(0,0,0,0.25);
  }
  .card-front { top: 72px; }
  .card-back { top: 509px; }

  .front-accent {
    position: absolute; left: 300px; top: -60px; width: 460px; height: 460px;
    border-radius: 50%;
    background: linear-gradient(135deg, var(--blue-light), var(--blue-mid) 55%, var(--blue-deep));
  }
  .wordmark {
    font-weight: 700; color: var(--navy); letter-spacing: 5px; text-transform: uppercase;
    line-height: 1;
  }
  .card-front .wordmark {
    position: absolute; left: 28px; top: 314px; font-size: 26px;
  }

  .brand-dot {
    position: absolute; left: 298px; top: 60px; width: 62px; height: 62px;
    border-radius: 50%; border: 5px solid var(--blue-mid);
  }
  .card-back .wordmark {
    position: absolute; left: 0; right: 0; top: 138px; text-align: center; font-size: 22px;
  }
  .person {
    position: absolute; right: 357px; top: 208px; text-align: right;
  }
  .person-name { font-size: 23px; font-weight: 700; color: var(--navy); letter-spacing: 1px; line-height: 1.1; }
  .person-title { font-size: 15px; font-weight: 400; color: var(--text-grey); letter-spacing: 0.8px; margin-top: 8px; }
  .divider {
    position: absolute; left: 335px; top: 198px; width: 2px; height: 74px; background: var(--divider);
  }
  .contact-list {
    position: absolute; left: 358px; top: 194px; list-style: none;
  }
  .contact-list li {
    display: flex; align-items: center; height: 20px;
    font-size: 15px; font-weight: 300; color: var(--text-grey);
  }
  .contact-list svg { width: 12px; height: 12px; margin-right: 10px; fill: none; stroke: var(--navy); stroke-width: 1.6; }
  .address {
    position: absolute; left: 0; right: 0; top: 323px; text-align: center;
    font-size: 15px; font-weight: 400; color: var(--text-dark); letter-spacing: 0.3px;
  }
</style>
</head>
<body>
<div class="canvas">
  <section class="card card-front">
    <div class="front-accent" role="img" aria-label="Large blue brand accent"></div>
    <div class="wordmark">SkyvornQ</div>
  </section>

  <section class="card card-back">
    <div class="brand-dot"></div>
    <div class="wordmark">SkyvornQ</div>
    <div class="person">
      <div class="person-name">DANIEL HARROW</div>
      <div class="person-title">Vice President</div>
    </div>
    <div class="divider"></div>
    <ul class="contact-list">
      <li><svg viewBox="0 0 12 12"><rect x="3" y="1" width="6" height="10" rx="1"/></svg>503-555-0142</li>
      <li><svg viewBox="0 0 12 12"><path d="M3 1 L5 4 L4 5 Q5 7 7 8 L8 7 L11 9 L9 11 Q3 10 1 3 Z"/></svg>503-555-0187</li>
      <li><svg viewBox="0 0 12 12"><rect x="1" y="3" width="10" height="7"/><path d="M1 3 L6 7 L11 3"/></svg>info@skyvornq.com</li>
      <li><svg viewBox="0 0 12 12"><circle cx="6" cy="6" r="5"/><path d="M1 6 H11 M6 1 Q3 6 6 11 M6 1 Q9 6 6 11"/></svg>www.skyvornq.com</li>
    </ul>
    <div class="address">4827 Trellis Hollow Road, Brinmoor Bay, Calvera, 34951</div>
  </section>
</div>
</body>
</html>
```